Candle Rental Business seeks new website design

We need a new website design for a Candle hire business. The business rents out pillar candles for events such as weddings and corporate events. Our main target market is weddings. The business name is Hire a Lantern. The business name does not have a logo design.

We would like a website that is light in colours and creates a warm atmosphere. The design needs to be elegant and upmarket. There are different size candles that we hire out, ranging from 10cm diameter to 20cm diameter, flat, tall etc. All our candles are white in colour. Its just the size that differs.

We would also like to include a section for hiring out decor such as glassvases, candlebras, overlays and chairs sachets, chair covers. However, this is not the businesses main focus but an additional offering to customers.

Target Market(s)

Wedding venues and brides. Corporate events. School dances.

Industry/Entity Type

Hospitality

Logo Text

Hire a Lantern

Number of Pages Required

1 page

Font styles to use
Sans Serif
Script

Requirements
Must have
• Pictures of pillar candles. Plain white candles. The website must centre around candles.
Nice to have
• Different examples of candle centrepieces
Should not have
• Pictures must not be of brides. Pictures of surrounding is perferable.

```html
<!DOCTYPE html>
<html lang="en">
<head>
<meta charset="utf-8">
<title>Hire a Lantern – Candle Hire</title>
<link href="https://fonts.googleapis.com/css2?family=Questrial&family=Lato:wght@400;700&family=Fredoka:wght@600&display=swap" rel="stylesheet">
<style>
:root{
  --orange:#f07d12;
  --amber:#f8b316;
  --ink:#222;
  --body:#555;
  --muted:#777;
  --cream:#f4f1e5;
  --grey-band:#ebebeb;
  --green:#7a9a32;
  --dark:#2e2e2e;
  --white:#fff;
}
*{box-sizing:border-box;margin:0;padding:0}
html,body{width:1200px;height:2727px;overflow:hidden;background:var(--white)}
body{position:relative;font-family:"Lato",sans-serif;color:var(--body)}
.abs{position:absolute}
.heading{font-family:"Questrial",sans-serif;color:var(--ink);font-weight:400}

/* header */
.site-header{left:0;top:0;width:1200px;height:86px;background:var(--white)}
.brand{left:80px;top:22px;display:flex;align-items:center;gap:14px}
.brand-mark{width:22px;height:22px;background:var(--orange);border-radius:50%}
.brand-name{font-family:"Questrial",sans-serif;font-size:38px;color:var(--ink)}
.account-links{right:82px;top:10px;display:flex;gap:30px;font-size:13px;color:var(--muted)}
.account-links span{display:flex;align-items:center;gap:7px}
.account-links i{display:inline-block;width:12px;height:12px;border:1.5px solid var(--muted);border-radius:2px}
.main-nav{right:80px;top:50px;display:flex;gap:36px;font-family:"Questrial",sans-serif;font-size:16px;color:var(--ink)}
.main-nav a{color:inherit;text-decoration:none;padding:3px 7px}
.main-nav .active{color:var(--orange);border:1.5px solid var(--orange)}

/* hero */
.hero{left:0;top:86px;width:1200px;height:534px;background:radial-gradient(ellipse at 50% 55%,#f6e3a6 0%,#c8a764 18%,#6e6040 40%,#3d2a26 70%,#5a1c1e 100%)}
.hero-arrow{top:320px;width:24px;height:40px}
.hero-banner{left:118px;top:568px;width:956px;height:52px;background:linear-gradient(90deg,rgba(240,125,18,0),var(--orange) 8%,var(--orange) 92%,rgba(240,125,18,0));text-align:center;font-family:"Fredoka",sans-serif;font-size:27px;line-height:52px;color:var(--white);letter-spacing:.3px}

/* about */
.about-title{left:0;top:666px;width:1200px;text-align:center;font-size:40px}
.about-text{left:92px;top:728px;width:1016px;text-align:center;font-size:14px;line-height:26px;color:var(--body)}
.read-more{left:0;top:834px;width:1200px;text-align:center;font-size:16px;color:var(--orange);text-decoration:underline}

/* services */
.services{left:0;top:902px;width:1200px;height:622px;background:var(--cream)}
.card{background:var(--white)}
.photo{display:block}
.card-title{font-family:"Questrial",sans-serif;font-size:26px;color:var(--ink)}
.card-text{font-size:13.5px;line-height:26px;color:var(--body)}
.btn{display:inline-block;background:var(--green);color:var(--white);font-size:12px;padding:0 16px;height:30px;line-height:30px}

/* how it works */
.how-title{left:0;top:1572px;width:1200px;text-align:center;font-size:40px}
.step{width:240px;text-align:center}
.step-circle{width:150px;height:150px;border-radius:50%;margin:0 auto;display:flex;align-items:center;justify-content:center}
.step-label{margin-top:22px;font-family:"Questrial",sans-serif;font-size:23px;line-height:30px;color:var(--muted)}
.orange{background:var(--orange)}
.amber{background:var(--amber)}

/* decor */
.decor{left:0;top:2000px;width:1200px;height:386px;background:var(--grey-band)}
.decor-title{left:0;top:2050px;width:1200px;text-align:center;font-size:40px}
.decor-tile{top:2154px;width:254px;height:188px}
.decor-tile .frame{position:absolute;inset:10px;border:1.5px solid rgba(255,255,255,.85)}
.decor-tile .label{position:absolute;inset:0;display:flex;align-items:center;justify-content:center;text-align:center;font-family:"Lato",sans-serif;font-weight:700;font-size:23px;line-height:30px;color:var(--white)}

/* footer */
.site-footer{left:0;top:2386px;width:1200px;height:290px;background:var(--cream)}
.foot-heading{font-size:14px;color:var(--ink);padding-bottom:8px;border-bottom:1px solid #ddd6c2}
.quick-links{list-style:none;font-size:12px;color:var(--body)}
.quick-links li{position:relative;padding-left:18px;margin-top:32px}
.quick-links li::before{content:"";position:absolute;left:2px;top:5px;width:5px;height:5px;border:1px solid var(--muted);border-radius:50%}
.contact-row{display:flex;gap:14px;align-items:flex-start;font-size:12.5px;line-height:18px;color:var(--body)}
.field{width:238px;border:1.5px solid #8b8b8b;background:var(--white);font-size:11px;color:var(--body);padding:3px 7px}
.submit{width:238px;height:34px;background:var(--orange);color:var(--white);font-size:14px;text-align:center;line-height:34px}
.social{display:flex;align-items:center;gap:12px;font-size:12px;margin-top:14px}
.social i{width:32px;height:32px;border-radius:50%;display:inline-block}
.bottom-bar{left:0;top:2676px;width:1200px;height:51px;background:var(--dark);color:#ddd;font-size:13px}
.card-chip{width:30px;height:20px;background:var(--white);border-radius:2px;font-size:6px;color:#333;text-align:center;line-height:20px}
</style>
</head>
<body>

<header class="abs site-header">
  <div class="abs brand"><span class="brand-mark"></span><span class="brand-name">Hire a Lantern</span></div>
  <div class="abs account-links"><span><i></i>Log In</span><span><i></i>Register</span></div>
  <nav class="abs main-nav"><a class="active">Home</a><a>About Us</a><a>Our Products</a><a>Contact Us</a></nav>
</header>

<section class="abs hero" role="img" aria-label="Table centrepiece: lit white pillar candle in a glass hurricane vase on cream roses and greenery, surrounded by wine glasses"></section>
<svg class="abs hero-arrow" style="left:26px" viewBox="0 0 24 40"><path d="M20 4 4 20l16 16" fill="none" stroke="#fff" stroke-width="2"/></svg>
<svg class="abs hero-arrow" style="left:1150px" viewBox="0 0 24 40"><path d="M4 4l16 16L4 36" fill="none" stroke="#fff" stroke-width="2"/></svg>
<div class="abs hero-banner">WE DESIGN, MANUFACTURE &amp; PERSONALISE DECORATIVE CANDLES</div>

<h2 class="abs heading about-title">About Us</h2>
<p class="abs about-text">We are a family owned and operated company and began making decorative candles for all occasions.&nbsp; All of our candles are individually hand made in our candle studio, situated in Elmsford, outside Harbourview.&nbsp; Our wax is local and of a very high quality, and dripless! Our wax is also made with a high melting point, which means it will not melt or bend in hot temperatures.</p>
<a class="abs read-more">Read More</a>

<section class="abs services"></section>
<article class="abs card" style="left:96px;top:960px;width:382px;height:500px">
  <div class="abs photo" style="left:18px;top:16px;width:346px;height:236px;background:linear-gradient(160deg,#e8e4da,#b9b3a4 55%,#6fa3b4)" role="img" aria-label="White pillar candles of varying heights in a glass bowl of blue stones on a set table"></div>
  <h3 class="abs card-title" style="left:18px;top:264px">Hire Candles</h3>
  <p class="abs card-text" style="left:18px;top:304px;width:346px">Do you love using candles for your events but tired of sorting old used candles or buying expensive the candles. Believe it or not you can now rent lorem is candles.All our candles come in different sizes and heights.You can add the ambience of.</p>
  <span class="abs btn" style="left:22px;top:452px">Read More</span>
</article>
<article class="abs card" style="left:498px;top:960px;width:615px;height:240px">
  <h3 class="abs card-title" style="left:18px;top:12px">Personalised Candles</h3>
  <p class="abs card-text" style="left:18px;top:50px;width:360px;font-size:13px;line-height:26px">Hire a Lantern provides the opportunity to give a thoughtful, meaningful gift at a friendly price point. This unique gift conveys the time and care you put into creating it. The recipient will enjoy the beautiful presentation and be reminded of the sentiment...</p>
  <span class="abs btn" style="left:20px;top:188px">Read More</span>
  <div class="abs photo" style="left:392px;top:16px;width:204px;height:204px;background:linear-gradient(150deg,#f4f1ee,#e6c9d4 50%,#f3ece6)" role="img" aria-label="Two personalised candles in glass jars with pink labels beside a rose"></div>
</article>
<article class="abs card" style="left:498px;top:1220px;width:615px;height:240px">
  <h3 class="abs card-title" style="left:18px;top:12px">Décor Hire</h3>
  <p class="abs card-text" style="left:18px;top:50px;width:380px;font-size:13px;line-height:26px">We hire a selection of overlays, chair sachets and chair covers as well as glassware and candelabras to compliment your décor.</p>
  <span class="abs btn" style="left:20px;top:142px">Read More</span>
  <div class="abs photo" style="left:392px;top:16px;width:204px;height:204px;background:radial-gradient(ellipse at 55% 55%,#f1e7b6,#6e7a48 45%,#5a2a2a)" role="img" aria-label="Candle centrepiece with cream roses and greenery among wine glasses"></div>
</article>

<h2 class="abs heading how-title">How It Works</h2>
<svg class="abs" style="left:246px;top:1672px" width="120" height="50" viewBox="0 0 120 50"><path d="M4 34C34 12 76 8 106 22" fill="none" stroke="#cfcfcf" stroke-width="3"/><path d="M94 10l14 13-18 5" fill="none" stroke="#cfcfcf" stroke-width="3"/></svg>
<svg class="abs" style="left:548px;top:1838px" width="110" height="50" viewBox="0 0 110 50"><path d="M4 20C36 36 70 34 100 14" fill="none" stroke="#cfcfcf" stroke-width="3"/><path d="M84 10l16 4-6 16" fill="none" stroke="#cfcfcf" stroke-width="3"/></svg>
<svg class="abs" style="left:842px;top:1672px" width="120" height="50" viewBox="0 0 120 50"><path d="M4 34C34 12 76 8 106 22" fill="none" stroke="#cfcfcf" stroke-width="3"/><path d="M94 10l14 13-18 5" fill="none" stroke="#cfcfcf" stroke-width="3"/></svg>

<div class="abs step" style="left:35px;top:1703px">
  <div class="step-circle orange"><svg width="50" height="86" viewBox="0 0 50 86"><path d="M25 4c6 8 6 14 0 18-6-4-6-10 0-18z" fill="#fff"/><rect x="8" y="30" width="34" height="52" rx="4" fill="#fff"/><path d="M8 48h34M8 64h34" stroke="#f07d12" stroke-width="3"/></svg></div>
  <div class="step-label">Choose your<br>Candle</div>
</div>
<div class="abs step" style="left:331px;top:1703px">
  <div class="step-circle amber"><svg width="70" height="90" viewBox="0 0 70 90"><path d="M22 8a6 6 0 0 1 12 0v34h4V34a6 6 0 0 1 12 0v10h2a6 6 0 0 1 12 0v20c0 14-10 24-24 24H38C22 88 10 76 6 62L2 48a6 6 0 0 1 11-4l9 14z" fill="#fff"/></svg></div>
  <div class="step-label">Book your<br>Candle</div>
</div>
<div class="abs step" style="left:631px;top:1703px">
  <div class="step-circle orange"><svg width="84" height="70" viewBox="0 0 84 70"><g transform="rotate(-14 42 35)"><rect x="6" y="16" width="72" height="40" rx="3" fill="#fff"/><rect x="12" y="22" width="60" height="28" rx="2" fill="none" stroke="#f07d12" stroke-width="3"/><circle cx="42" cy="36" r="8" fill="#f07d12"/></g></svg></div>
  <div class="step-label">Make<br>payment</div>
</div>
<div class="abs step" style="left:925px;top:1703px">
  <div class="step-circle amber"><svg width="70" height="100" viewBox="0 0 70 100"><path d="M35 4c5 7 5 12 0 16-5-4-5-9 0-16z" fill="#fff"/><rect x="22" y="26" width="26" height="44" rx="3" fill="none" stroke="#fff" stroke-width="4"/><path d="M8 72h54l-6 10H14z" fill="none" stroke="#fff" stroke-width="4"/><path d="M22 92h26" stroke="#fff" stroke-width="4"/></svg></div>
  <div class="step-label" style="margin-top:12px">Light Up<br>Your Event</div>
</div>

<section class="abs decor"></section>
<h2 class="abs heading decor-title">Our Hiring Out Decor</h2>
<div class="abs decor-tile" style="left:80px;background:linear-gradient(135deg,#2d3438,#6b6f6c 50%,#2a2e30)" role="img" aria-label="Lit candles in tall glass vases"><div class="frame"></div><div class="label">Glass Vases</div></div>
<div class="abs decor-tile" style="left:342px;background:linear-gradient(135deg,#4d4330,#8a7a55 50%,#5a4e38)" role="img" aria-label="Glass candelabras on a table"><div class="frame"></div><div class="label">Candle Bras</div></div>
<div class="abs decor-tile" style="left:604px;background:linear-gradient(135deg,#3a3a38,#8d8c86 50%,#3c3b39)" role="img" aria-label="Lace overlay tied as a chair sash"><div class="frame"></div><div class="label">Overlays &amp;<br>Chairs Sachets</div></div>
<div class="abs decor-tile" style="left:866px;background:linear-gradient(135deg,#3b3032,#b89aa2 50%,#4a3a3e)" role="img" aria-label="Rows of white chair covers with pink sashes"><div class="frame"></div><div class="label">Chair Covers</div></div>

<footer class="abs site-footer"></footer>
<div class="abs" style="left:80px;top:2424px;width:140px">
  <div class="foot-heading">Quick Links</div>
  <ul class="quick-links"><li style="margin-top:16px">Home</li><li>About Us</li><li>Our Products</li><li>Contact Us</li></ul>
</div>
<div class="abs" style="left:304px;top:2424px;width:220px">
  <div class="foot-heading">Contact Details</div>
  <div class="contact-row" style="margin-top:14px"><svg width="20" height="22" viewBox="0 0 20 22"><path d="M10 21s-7-7-7-12a7 7 0 0 1 14 0c0 5-7 12-7 12z" fill="none" stroke="#777" stroke-width="1.6"/><circle cx="10" cy="9" r="2.5" fill="#777"/></svg><span>1/23 Lorem Ips Dolo, Consecer<br>wererr Nonuy - 12345</span></div>
  <div class="contact-row" style="margin-top:38px"><svg width="20" height="20" viewBox="0 0 20 20"><path d="M5 2l3 4-2 2c1 3 3 5 6 6l2-2 4 3-2 3C9 18 2 11 2 4z" fill="none" stroke="#777" stroke-width="1.6"/></svg><span style="font-size:14px">123-456-7890</span></div>
  <div class="contact-row" style="margin-top:40px"><svg width="20" height="14" viewBox="0 0 20 14"><rect x="1" y="1" width="18" height="12" fill="none" stroke="#777" stroke-width="1.6"/><path d="M1 1l9 7 9-7" fill="none" stroke="#777" stroke-width="1.6"/></svg><span>info@companyname.com</span></div>
</div>
<div class="abs" style="left:651px;top:2424px;width:248px">
  <div class="foot-heading">Quick Inquiry</div>
  <div class="field" style="margin-top:12px;height:28px">Name</div>
  <div class="field" style="margin-top:8px;height:28px">Phone</div>
  <div class="field" style="margin-top:8px;height:48px">Message</div>
  <div class="submit" style="margin-top:10px">Submit</div>
</div>
<div class="abs" style="left:1002px;top:2424px;width:118px">
  <div class="foot-heading">Follow Us</div>
  <div class="social" style="color:#3b5ba8"><i style="background:#3b5ba8"></i>Friendpage</div>
  <div class="social" style="color:#3fa9e0"><i style="background:#3fa9e0"></i>Chirpline</div>
  <div class="social" style="color:#2a7db5"><i style="background:#2a7db5"></i>WorkCircle</div>
  <div class="social" style="color:#d24a3a"><i style="background:#d24a3a"></i>CirclePlus</div>
</div>

<div class="abs bottom-bar">
  <span class="abs" style="left:80px;top:17px">Copyright © 2016 Hire a Lantern. All Rights Reserved.</span>
  <span class="abs" style="left:910px;top:17px">We Accept:</span>
  <div class="abs" style="left:1006px;top:15px;display:flex;gap:3px">
    <span class="card-chip">CardOne</span><span class="card-chip">PayLink</span><span class="card-chip">Credo</span><span class="card-chip">Findr</span>
  </div>
</div>

</body>
</html>
```